RTavenor Business Cards & Letterhead

I have a logo but need a design for some new business cards. We are a Design-Build Firm that specializes in the design and construction of commercial projects.
the cards need to be professional. no cartoon stuff.
i would like to have the cards in AI format so I can update the card as needed. Logo is provided.
Our Address is: 4187 Marlowe Ct. Apex, North Carolina 27614

```html
<!DOCTYPE html>
<html lang="en">
<head>
<meta charset="utf-8">
<title>RTavenor Business Card</title>
<link href="https://fonts.googleapis.com/css2?family=Montserrat:wght@500;700;800&display=swap" rel="stylesheet">
<style>
  :root {
    --bg: #d9d9d9;
    --card: #f7f7f7;
    --card-back: #ececec;
    --ink: #555658;
    --ink-soft: #5f6062;
    --brand-blue: #165a8c;
    --brand-blue-light: #4f8fb6;
    --rule: #5a5a5a;
  }
  * { box-sizing: border-box; margin: 0; padding: 0; }
  html, body { width: 1200px; height: 1200px; overflow: hidden; }
  body {
    background: var(--bg);
    font-family: "Montserrat", sans-serif;
    display: flex;
    flex-direction: column;
    align-items: center;
    justify-content: center;
    gap: 60px;
  }
  .card {
    position: relative;
    width: 840px;
    height: 480px;
    border-radius: 28px;
    overflow: hidden;
    box-shadow: 0 10px 30px rgba(0,0,0,0.18);
  }
  .card-front { background: var(--card); display: flex; align-items: center; justify-content: center; }
  .card-back { background: var(--card-back); }
  .wordmark {
    display: flex; align-items: center; gap: 14px;
    color: var(--ink); font-weight: 800; letter-spacing: 2px;
  }
  .wordmark-square { background: var(--brand-blue-light); }
  .wordmark-large { font-size: 74px; }
  .wordmark-large .wordmark-square { width: 40px; height: 40px; }
  .wordmark-small { font-size: 40px; gap: 9px; letter-spacing: 1px; }
  .wordmark-small .wordmark-square { width: 22px; height: 22px; }
  .back-logo { position: absolute; left: 70px; top: 205px; }
  .divider { position: absolute; left: 390px; top: 80px; width: 2px; height: 230px; background: var(--rule); }
  .details { position: absolute; left: 430px; top: 66px; color: var(--ink-soft); }
  .person-name { color: var(--brand-blue); font-weight: 800; font-size: 38px; letter-spacing: 0.5px; }
  .person-title { font-weight: 500; font-size: 20px; margin: 4px 0 0 14px; }
  .address { font-weight: 500; font-size: 21px; line-height: 1.3; margin: 16px 0 12px 30px; }
  .contact-list { list-style: none; margin-left: 40px; font-weight: 500; font-size: 21px; }
  .contact-list li { display: flex; align-items: center; gap: 12px; line-height: 1.45; }
  .contact-list svg { width: 18px; height: 18px; fill: var(--brand-blue); flex-shrink: 0; }
  .wave { position: absolute; left: 0; bottom: 0; width: 840px; height: 480px; }
</style>
</head>
<body>
  <section class="card card-front">
    <div class="wordmark wordmark-large">
      <span class="wordmark-square"></span><span>RTAVENOR</span>
    </div>
  </section>

  <section class="card card-back">
    <svg class="wave" viewBox="0 0 840 480" preserveAspectRatio="none" aria-hidden="true">
      <defs>
        <linearGradient id="waveFill" x1="0" y1="0" x2="1" y2="0">
          <stop offset="0" stop-color="#4f8fb6"/>
          <stop offset="0.5" stop-color="#1e6597"/>
          <stop offset="1" stop-color="#12507f"/>
        </linearGradient>
      </defs>
      <path d="M0 405 C 200 435, 380 420, 520 375 C 650 335, 760 330, 840 340 L840 480 L0 480 Z" fill="url(#waveFill)"/>
    </svg>

    <div class="wordmark wordmark-small back-logo">
      <span class="wordmark-square"></span><span>RTAVENOR</span>
    </div>

    <div class="divider"></div>

    <div class="details">
      <h1 class="person-name">Rowan Tavenor</h1>
      <p class="person-title">President</p>
      <p class="address">4187 Marlowe Ct. Apex,<br>North Carolina 27614</p>
      <ul class="contact-list">
        <li>
          <svg viewBox="0 0 24 24"><path d="M6.6 10.8a15 15 0 0 0 6.6 6.6l2.2-2.2a1 1 0 0 1 1-.25 11.4 11.4 0 0 0 3.6.57 1 1 0 0 1 1 1V20a1 1 0 0 1-1 1A17 17 0 0 1 3 4a1 1 0 0 1 1-1h3.5a1 1 0 0 1 1 1c0 1.25.2 2.45.57 3.57a1 1 0 0 1-.25 1z"/></svg>
          (405)-555-0147
        </li>
        <li>
          <svg viewBox="0 0 24 24"><path d="M2 5h20v2l-10 7L2 7z M2 9l10 7 10-7v10H2z"/></svg>
          info@rtavenor.com
        </li>
        <li>
          <svg viewBox="0 0 24 24"><path d="M12 2a10 10 0 1 0 0 20 10 10 0 0 0 0-20zm-1 17.9A8 8 0 0 1 4.1 13H7c.1 2.5.8 4.9 1.9 6.9zM4.1 11A8 8 0 0 1 11 4.1V11zm8.9-6.9A8 8 0 0 1 19.9 11H13zM13 19.9V13h6.9a8 8 0 0 1-6.9 6.9z"/></svg>
          www.rtavenor.com
        </li>
      </ul>
    </div>
  </section>
</body>
</html>
```